Trade Show booth design

I need the following designs for my trade booth:
1. backboard design 3m Wx2mH
2. Tressle table, tablecloth front panel design 1800W x 740mmH
3. Pop-up banner. I have included our logos and some design content ideas:
Headline:
"Cleaner Classrooms. Safer Schools."
Subheadline:
"Specialist Cleaning Solutions for Education Facilities"
Key Points to Grab Attention:
Healthy Environments: Create hygienic, safe learning spaces for students and staff with our expert cleaning services.
Tailored to Your Needs: Custom cleaning plans for classrooms, labs, libraries, and sports facilities.
Affordable Excellence: Premium results without premium costs – tailored plans mean you only pay for what you need.
Safety First: All staff are trained, highly vetted, and hold current Working with Children Checks (WWCC).
Eco-Conscious Cleaning: Using non-toxic, eco-friendly products certified for health and safety.
What Schools Really Need:
Reliability: Consistent, high-quality cleaning from a trusted provider.
Cost-Effectiveness: Solutions that fit tight budgets while maintaining high standards.
Expertise: Over 30 years of experience in education facility cleaning.
Disinfection Services: Focus on high-touch areas to reduce the spread of germs and ensure peace of mind.
Visual Elements:
Images of bright, clean classrooms, a happy teacher welcoming students, or students collaborating in a spotless library.
Icons representing safety (shield), hygiene (sparkling star), and eco-friendliness (leaf).
Your logo with the tagline: "Trusted by Queensland Schools Since 1995."
Call-to-Action:
"Visit us to discuss your school’s cleaning needs and book a FREE consultation."
Include contact details: Phone: 1300 594 316 | Website: www.brightmorefacility.com.au
Target Market(s)
Education sector
Industry/Entity Type
Commercial Cleaning
Font styles to use
Other font styles liked:
- Montserrat
Look and feel

```html
<!DOCTYPE html>
<html lang="en">
<head>
<meta charset="utf-8">
<title>Brightmore Facility Cleaning – Education Backboard</title>
<link rel="stylesheet" href="https://fonts.googleapis.com/css2?family=Montserrat:wght@400;500;600;700;800&display=swap">
<style>
  :root {
    --stage: #cce0fb;
    --navy: #1b3f63;
    --navy-deep: #1a3a5c;
    --photo-light: #8c97b3;
    --photo-mid: #5f6f92;
    --silver-light: #f2f2f2;
    --silver-dark: #b9bcc2;
    --ring: #8d93a3;
    --white: #ffffff;
  }
  * { box-sizing: border-box; margin: 0; padding: 0; }
  html, body { width: 1200px; height: 600px; overflow: hidden; }
  body {
    background: var(--stage);
    font-family: "Montserrat", sans-serif;
    position: relative;
  }
  .board {
    position: absolute;
    left: 184px; top: 22px;
    width: 832px; height: 554px;
    background: var(--navy);
    overflow: hidden;
    color: var(--white);
  }
  .classroom-photo {
    position: absolute;
    left: 0; top: 250px; width: 832px; height: 304px;
    background: linear-gradient(180deg, var(--navy) 0%, var(--photo-mid) 40%, var(--photo-light) 75%, var(--photo-mid) 100%);
  }
  .waves { position: absolute; left: 0; top: 0; }
  .brand {
    position: absolute; top: 30px; left: 0; width: 100%;
    display: flex; justify-content: center; align-items: center; gap: 12px;
  }
  .brand-dot { width: 34px; height: 34px; border-radius: 50%; background: var(--white); }
  .brand-name { font-weight: 600; font-size: 24px; letter-spacing: 0.5px; }
  .headline {
    position: absolute; top: 101px; left: 0; width: 100%;
    text-align: center; font-weight: 800; font-size: 40px; line-height: 36px;
    letter-spacing: 0.3px;
  }
  .subhead-band {
    position: absolute; left: 77px; top: 182px; width: 678px; height: 25px;
    background: linear-gradient(90deg, var(--silver-dark), var(--silver-light) 30%, var(--silver-light) 70%, var(--silver-dark));
    border-radius: 14px 4px 14px 4px;
    color: var(--navy); font-weight: 500; font-size: 19px; line-height: 25px;
    text-align: center;
  }
  .features { position: absolute; top: 232px; left: 0; width: 100%; }
  .feature {
    position: absolute; width: 220px; text-align: center;
    font-size: 15.5px; line-height: 19.5px;
  }
  .feature strong { font-weight: 800; }
  .feature-icon { display: block; margin: 0 auto 6px; }
  .feature--years { left: 72px; }
  .feature--trusted { left: 306px; }
  .feature--eco { left: 539px; }
  .cta {
    position: absolute; right: 34px; top: 469px; text-align: right;
    font-size: 13.6px; line-height: 16.5px;
  }
  .contact {
    position: absolute; right: 30px; top: 504px;
    font-size: 19px; display: flex; align-items: center; gap: 5px;
  }
</style>
</head>
<body>
  <main class="board">
    <div class="classroom-photo" role="img" aria-label="Photo of a clean, empty classroom with rows of desks and chairs"></div>

    <svg class="waves" width="832" height="554" viewBox="0 0 832 554" aria-hidden="true">
      <defs>
        <linearGradient id="silver" x1="0" y1="0" x2="1" y2="0">
          <stop offset="0" stop-color="#c9cbd0"/>
          <stop offset="0.4" stop-color="#f4f4f4"/>
          <stop offset="1" stop-color="#bfc2c8"/>
        </linearGradient>
      </defs>
      <path d="M0,369 C90,470 210,545 340,536 C520,522 620,425 832,415 L832,470 C620,450 520,525 340,556 L0,554 Z" fill="url(#silver)"/>
      <path d="M0,455 C110,535 240,562 350,548 C520,525 630,440 832,472 L832,554 L0,554 Z" fill="var(--navy-deep)"/>
    </svg>

    <header class="brand">
      <span class="brand-dot"></span>
      <span class="brand-name">Brightmore Facility Cleaning</span>
    </header>

    <h1 class="headline">CREATING CLEANER,<br>SAFER LEARNING ENVIRONMENTS</h1>
    <p class="subhead-band">Specialists in Education Facility Cleaning &amp; Eco-Friendly Services</p>

    <section class="features">
      <div class="feature feature--years">
        <svg class="feature-icon" width="80" height="80" viewBox="0 0 80 80" aria-hidden="true">
          <circle cx="40" cy="40" r="38" fill="var(--navy)" stroke="var(--ring)" stroke-width="4"/>
          <circle cx="40" cy="40" r="32" fill="none" stroke="#fff" stroke-width="0.8" stroke-dasharray="2 2"/>
          <circle cx="40" cy="38" r="13" fill="none" stroke="#fff" stroke-width="2"/>
          <path d="M33,38 l5,5 l9,-10" fill="none" stroke="#fff" stroke-width="2.4" stroke-linecap="round" stroke-linejoin="round"/>
        </svg>
        Over <strong>30 years</strong><br>of expertise in<br>commercial cleaning.
      </div>
      <div class="feature feature--trusted">
        <svg class="feature-icon" width="80" height="80" viewBox="0 0 80 80" aria-hidden="true">
          <circle cx="40" cy="40" r="38" fill="var(--navy)" stroke="var(--ring)" stroke-width="4"/>
          <circle cx="40" cy="40" r="32" fill="none" stroke="#fff" stroke-width="0.8" stroke-dasharray="2 2"/>
          <g fill="none" stroke="#fff" stroke-width="1.4" stroke-linejoin="round">
            <path d="M30,22 l1.5,3 3.2,.4 -2.4,2.2 .6,3.2 -2.9,-1.6 -2.9,1.6 .6,-3.2 -2.4,-2.2 3.2,-.4z"/>
            <path d="M40,19 l1.5,3 3.2,.4 -2.4,2.2 .6,3.2 -2.9,-1.6 -2.9,1.6 .6,-3.2 -2.4,-2.2 3.2,-.4z"/>
            <path d="M50,22 l1.5,3 3.2,.4 -2.4,2.2 .6,3.2 -2.9,-1.6 -2.9,1.6 .6,-3.2 -2.4,-2.2 3.2,-.4z"/>
            <circle cx="40" cy="42" r="6"/>
            <path d="M29,60 c0,-8 5,-11 11,-11 s11,3 11,11z"/>
          </g>
        </svg>
        Trusted by <strong>schools,<br>universities, and TAFEs</strong><br>across Queensland.
      </div>
      <div class="feature feature--eco">
        <svg class="feature-icon" width="80" height="80" viewBox="0 0 80 80" aria-hidden="true">
          <circle cx="40" cy="40" r="38" fill="var(--navy)" stroke="var(--ring)" stroke-width="4"/>
          <circle cx="40" cy="40" r="32" fill="none" stroke="#fff" stroke-width="0.8" stroke-dasharray="2 2"/>
          <path d="M20,46 C26,30 44,24 60,28 C60,46 46,58 30,54 C36,48 42,44 50,40 C40,42 30,46 20,46 Z" fill="#fff"/>
        </svg>
        <strong>100% Carbon Neutral<br>and Eco-Certified</strong><br>Services.
      </div>
    </section>

    <p class="cta">Visit us to discuss your school’s cleaning needs<br>and book a FREE consultation.</p>
    <p class="contact">
      <svg width="11" height="18" viewBox="0 0 11 18" aria-hidden="true"><rect x="1" y="1" width="9" height="16" rx="1.5" fill="none" stroke="#fff" stroke-width="1.3"/></svg>
      1300 594 316 |
      <svg width="16" height="16" viewBox="0 0 16 16" aria-hidden="true"><g fill="none" stroke="#fff" stroke-width="1.1"><circle cx="8" cy="8" r="7"/><ellipse cx="8" cy="8" rx="3" ry="7"/><path d="M1,8 h14 M2.5,4.5 h11 M2.5,11.5 h11"/></g></svg>
      www.brightmorefacility.com.au
    </p>
  </main>
</body>
</html>
```